business cards and stationary
Kelvatri Motion Group
Professional
Domenic R. Haslow, D.C.
Chiropractor
4817 Tamsworth Glade Avenue
Los Angeles, CA 90213
drhaslow@kelvatrimotion.com
Kelvatrimotion.com
CA86271
map of location
logo file .AI

```html
<!DOCTYPE html>
<html lang="en">
<head>
<meta charset="utf-8">
<title>Kelvatri Motion Group — Business Cards and Stationery</title>
<link href="https://fonts.googleapis.com/css2?family=Montserrat:wght@700&family=Open+Sans:wght@400;600&display=swap" rel="stylesheet">
<style>
:root{
  --stage:#1b1b1c;
  --stage-light:#2b2b2d;
  --orange:#f7931e;
  --orange-deep:#e87a10;
  --gray:#6d6e71;
  --gray-light:#a7a9ac;
  --paper:#ffffff;
  --ink:#4a4a4c;
  --label:#b9b9b9;
  --map-a:#ebe7dc;
  --map-b:#d3cfc2;
}
*{box-sizing:border-box;margin:0;padding:0}
html,body{width:1200px;height:437px;overflow:hidden}
body{background:radial-gradient(ellipse at 50% 40%,var(--stage-light),var(--stage) 70%);font-family:"Open Sans",Arial,sans-serif;color:var(--ink);position:relative}
.piece{position:absolute;background:var(--paper);overflow:hidden;box-shadow:0 2px 6px rgba(0,0,0,.55)}
.piece>svg.shape{position:absolute;inset:0;width:100%;height:100%}
.brand-name{font-family:"Montserrat",Arial,sans-serif;font-weight:700;color:var(--orange);letter-spacing:.5px;position:absolute;line-height:1}
.brand-name.on-orange{color:var(--paper)}
.label{position:absolute;color:var(--label);font-size:7px;text-align:center;white-space:nowrap}
.tiny{position:absolute;font-size:4px;line-height:1.5;color:var(--ink);white-space:nowrap}
.tiny.on-orange{color:var(--paper)}
.tiny.right{text-align:right}
.tiny.center{text-align:center;left:0;right:0}

/* business cards */
.card-front{left:19px;top:70px;width:89px;height:96px}
.card-front .name-band{position:absolute;left:0;right:0;top:0;height:13px;background:var(--gray);color:var(--paper);font-size:4.6px;font-weight:600;text-align:right;padding:4px 5px 0 0}
.card-front .brand-name{left:7px;top:38px;font-size:13px}
.card-front .contact{right:5px;top:17px}
.card-back-map{left:19px;top:192px;width:89px;height:58px;background:linear-gradient(135deg,var(--map-a),var(--map-b))}
.card-back-brand{left:19px;top:270px;width:89px;height:60px;background:var(--orange)}
.card-back-brand .brand-name{left:0;right:0;top:24px;text-align:center;font-size:14px}

/* letterheads */
.letterhead-one{left:307px;top:7px;width:173px;height:350px}
.letterhead-one .brand-name{left:11px;top:15px;font-size:17px}
.letterhead-one .contact{right:7px;top:9px}
.letterhead-two{left:564px;top:7px;width:168px;height:350px}
.letterhead-two .brand-name{left:11px;top:13px;font-size:17px}
.footer{bottom:6px}

/* envelopes */
.envelope{width:222px}
.envelope-flap-gray{left:948px;top:12px;height:88px}
.envelope-flap-orange{left:958px;top:108px;height:82px}
.envelope-back{left:948px;top:197px;height:86px}
.envelope-front{left:952px;top:283px;height:75px}
.envelope-front .brand-name{left:10px;top:27px;font-size:15px}
.envelope-front .return{left:11px;top:46px}
</style>
</head>
<body>

<!-- card front -->
<section class="piece card-front" aria-label="Business card front">
  <svg class="shape" viewBox="0 0 89 96" preserveAspectRatio="none" aria-hidden="true">
    <path d="M0 78 Q40 62 89 70 L89 96 L0 96Z" fill="var(--orange)"/>
    <path d="M0 74 Q40 58 89 66" stroke="var(--gray-light)" stroke-width="1.2" fill="none"/>
  </svg>
  <div class="name-band">Domenic R. Haslow, D.C.</div>
  <div class="tiny right contact">Chiropractor<br>4817 Tamsworth Glade Avenue<br>Los Angeles, CA 90213<br>Tel 310.555.0148<br>Fax 310.555.0149<br>drhaslow@kelvatrimotion.com</div>
  <div class="brand-name">Kelvatri</div>
  <div class="tiny center on-orange" style="bottom:4px">Kelvatrimotion.com · CA86271</div>
</section>
<div class="label" style="left:19px;top:170px;width:89px">Card Front</div>

<!-- card back: map -->
<div class="piece card-back-map" role="img" aria-label="Street map showing the clinic location on Tamsworth Glade Avenue, Los Angeles"></div>
<div class="label" style="left:19px;top:254px;width:89px">Card Back Option #1</div>

<!-- card back: brand -->
<section class="piece card-back-brand" aria-label="Business card back">
  <div class="brand-name on-orange">Kelvatri</div>
</section>
<div class="label" style="left:19px;top:334px;width:89px">Card Back Option #2</div>

<!-- letterhead one -->
<section class="piece letterhead-one" aria-label="Letterhead option one">
  <svg class="shape" viewBox="0 0 173 350" preserveAspectRatio="none" aria-hidden="true">
    <path d="M78 0 L173 0 L173 44 Q120 40 92 24 Q82 14 78 0Z" fill="var(--orange)"/>
    <path d="M0 46 Q90 52 173 48" stroke="var(--gray-light)" stroke-width="1" fill="none"/>
    <path d="M0 326 Q90 308 173 318 L173 350 L0 350Z" fill="var(--orange)"/>
    <path d="M0 320 Q90 302 173 312" stroke="var(--gray)" stroke-width="2" fill="none"/>
  </svg>
  <div class="brand-name">Kelvatri</div>
  <div class="tiny right on-orange contact">Domenic R. Haslow, D.C.<br>4817 Tamsworth Glade Avenue<br>Los Angeles, CA 90213<br>drhaslow@kelvatrimotion.com</div>
  <div class="tiny center on-orange footer">T 310.555.0148 · F 310.555.0149 · Kelvatrimotion.com</div>
</section>
<div class="label" style="left:307px;top:362px;width:173px">Letterhead Option #1</div>

<!-- letterhead two -->
<section class="piece letterhead-two" aria-label="Letterhead option two">
  <svg class="shape" viewBox="0 0 168 350" preserveAspectRatio="none" aria-hidden="true">
    <path d="M0 0 L168 0 L168 30 Q100 50 0 40Z" fill="var(--orange)"/>
    <path d="M0 44 Q100 54 168 34" stroke="var(--gray)" stroke-width="2" fill="none"/>
    <path d="M0 336 Q84 328 168 334" stroke="var(--gray)" stroke-width="1.5" fill="none"/>
    <path d="M0 341 Q84 333 168 339 L168 350 L0 350Z" fill="var(--orange)"/>
  </svg>
  <div class="brand-name on-orange">Kelvatri</div>
  <div class="tiny center" style="bottom:18px">4817 Tamsworth Glade Avenue, Los Angeles, CA 90213</div>
  <div class="tiny center" style="bottom:13px">T 310.555.0148 · F 310.555.0149 · Kelvatrimotion.com</div>
</section>
<div class="label" style="left:564px;top:362px;width:168px">Letterhead Option #2</div>

<!-- envelopes -->
<section class="piece envelope envelope-flap-gray" aria-label="Envelope back, gray flap">
  <svg class="shape" viewBox="0 0 222 88" preserveAspectRatio="none" aria-hidden="true">
    <path d="M0 0 L222 0 L222 22 Q111 48 0 22Z" fill="var(--gray)"/>
    <path d="M0 30 Q111 56 222 30" stroke="var(--gray-light)" stroke-width="1" fill="none"/>
  </svg>
  <div class="tiny center" style="top:44px">drhaslow@kelvatrimotion.com</div>
</section>

<section class="piece envelope envelope-flap-orange" aria-label="Envelope back, orange flap">
  <svg class="shape" viewBox="0 0 222 82" preserveAspectRatio="none" aria-hidden="true">
    <path d="M0 0 L222 0 L222 20 Q111 46 0 20Z" fill="var(--orange)"/>
    <path d="M0 26 Q111 52 222 26" stroke="var(--gray)" stroke-width="2" fill="none"/>
  </svg>
  <div class="tiny center" style="top:46px">Kelvatrimotion.com</div>
</section>

<section class="piece envelope envelope-back" aria-label="Envelope back, plain">
  <svg class="shape" viewBox="0 0 222 86" preserveAspectRatio="none" aria-hidden="true">
    <path d="M0 0 L222 0 L222 18 Q111 40 0 18Z" fill="#f1f1f2"/>
    <path d="M0 18 Q111 40 222 18" stroke="var(--gray-light)" stroke-width="1" fill="none"/>
    <path d="M0 76 Q111 66 222 74 L222 86 L0 86Z" fill="var(--gray)"/>
  </svg>
</section>

<section class="piece envelope envelope-front" aria-label="Envelope front">
  <svg class="shape" viewBox="0 0 222 75" preserveAspectRatio="none" aria-hidden="true">
    <path d="M0 0 L222 0 L222 14 Q111 30 0 20Z" fill="var(--orange)"/>
    <path d="M0 24 Q111 34 222 18" stroke="var(--gray)" stroke-width="1.5" fill="none"/>
  </svg>
  <div class="brand-name">Kelvatri</div>
  <div class="tiny return">4817 Tamsworth Glade Avenue<br>Los Angeles, CA 90213</div>
</section>
<div class="label" style="left:948px;top:362px;width:222px">Envelope Options</div>

</body>
</html>
```